Duct Manufacturing Company new to the industry needs business card and stationary design

we are sheet metal duct manufacturers looking for a business card design to fit my new business logo.
nothing to crazy that will date, but want it to stand out from the crowed.
I'm sure you guys will work it out.

Contact Information for Business Card

Glen Marsh
Director

Address
17 Dorwell St
Larkfield NRT 4417

0438 760 514

Sales@flowbend.com.au

Font styles to use
Other font styles liked:
• BankGothic md bt

Requirements
Nice to have
• Like the idea of corner rounded to match logo
• like to keep colours flowing
• font I like sharp square not rounded

```html
<!DOCTYPE html>
<html lang="en">
<head>
<meta charset="utf-8">
<title>Flowbend Industries – Business Card</title>
<link rel="stylesheet" href="https://fonts.googleapis.com/css2?family=Michroma&family=Montserrat:wght@400;500&display=swap">
<style>
  :root {
    --backdrop: #a9a9aa;
    --paper: #fbfbfb;
    --brand-blue: #1a6fbd;
    --blue-light: #1489cf;
    --blue-deep: #1b4a95;
    --green-deep: #1a9a3c;
    --green-light: #8cc63f;
    --ink-white: #ffffff;
    --ink-soft: #e6eef8;
  }
  * { box-sizing: border-box; margin: 0; padding: 0; }
  html, body { width: 1200px; height: 1200px; overflow: hidden; }
  body {
    background: var(--backdrop);
    position: relative;
    font-family: "Montserrat", sans-serif;
  }
  .card {
    position: absolute;
    width: 712px;
    height: 419px;
    border-radius: 22px;
    background: var(--paper);
    overflow: hidden;
  }
  .card--front { left: 238px; top: 118px; }
  .card--back  { left: 230px; top: 644px; }

  .wordmark {
    font-family: "Michroma", sans-serif;
    color: var(--brand-blue);
    text-transform: uppercase;
  }
  .front-mark {
    position: absolute;
    left: 0; right: 0; top: 150px;
    display: flex; flex-direction: column; align-items: center; gap: 14px;
  }
  .front-mark .mark-dot {
    width: 52px; height: 52px; border-radius: 50%;
    background: var(--brand-blue);
  }
  .front-mark .wordmark { font-size: 30px; letter-spacing: 2px; line-height: 1.3; text-align: center; }

  .front-stripe {
    position: absolute; left: 0; right: 0; bottom: 0; height: 18px;
    background: linear-gradient(90deg, var(--green-deep) 0%, var(--green-light) 55%, var(--green-light) 66%, var(--ink-white) 66%, var(--ink-white) 67%, var(--blue-light) 67%, var(--blue-deep) 100%);
  }

  .back-mark {
    position: absolute; left: 0; right: 0; top: 74px;
    display: flex; align-items: center; justify-content: center; gap: 18px;
  }
  .back-mark .mark-dot {
    width: 44px; height: 44px; border-radius: 50%;
    background: var(--brand-blue);
  }
  .back-mark .wordmark { font-size: 27px; letter-spacing: 1.5px; }

  .contact-panel {
    position: absolute; left: 0; right: 0; top: 204px; bottom: 0;
    border-top: 4px solid var(--green-deep);
    background: linear-gradient(180deg, var(--blue-light) 0%, var(--brand-blue) 45%, var(--blue-deep) 100%);
    color: var(--ink-white);
  }
  .person-name {
    position: absolute; left: 40px; top: 30px;
    font-family: "Michroma", sans-serif; font-size: 21px; font-weight: 400; letter-spacing: 1.5px;
    text-transform: uppercase;
  }
  .person-role {
    position: absolute; left: 40px; top: 64px;
    font-size: 16.5px; color: var(--ink-soft);
  }
  .contact-list, .address {
    position: absolute; top: 108px;
    list-style: none; font-size: 17.5px; line-height: 25.5px; letter-spacing: 0.3px;
  }
  .contact-list { left: 40px; }
  .contact-list li { display: flex; align-items: center; gap: 18px; }
  .contact-list svg { width: 16px; height: 16px; fill: var(--ink-white); }
  .address { left: 348px; font-style: normal; }
</style>
</head>
<body>
  <section class="card card--front">
    <div class="front-mark">
      <span class="mark-dot"></span>
      <div class="wordmark">Flowbend<br>Industries</div>
    </div>
    <div class="front-stripe"></div>
  </section>

  <section class="card card--back">
    <div class="back-mark">
      <span class="mark-dot"></span>
      <span class="wordmark">Flowbend Industries</span>
    </div>
    <div class="contact-panel">
      <h1 class="person-name">Glen Marsh</h1>
      <p class="person-role">Director</p>
      <ul class="contact-list">
        <li>
          <svg viewBox="0 0 16 16" aria-hidden="true"><path d="M1 5c0-2 3-3 7-3s7 1 7 3v1h-3.5V4.5h-7V6H1z M4 7h8l2 7H2z M8 8.5a2 2 0 1 0 0.01 0z"/></svg>
          0438 760 514
        </li>
        <li>
          <svg viewBox="0 0 16 16" aria-hidden="true"><path d="M8 1a7 7 0 1 0 0.01 0zM3 5h2.3a11 11 0 0 0-.3 2.3H2.3A6 6 0 0 1 3 5zm3.3 0h3.4a10 10 0 0 1 .3 2.3H6a10 10 0 0 1 .3-2.3zm4.4 0H13a6 6 0 0 1 .7 2.3H11a11 11 0 0 0-.3-2.3zM2.3 8.7H5a11 11 0 0 0 .3 2.3H3a6 6 0 0 1-.7-2.3zm3.7 0h4a10 10 0 0 1-.3 2.3H6.3A10 10 0 0 1 6 8.7zm5 0h2.7A6 6 0 0 1 13 11h-2.3a11 11 0 0 0 .3-2.3z"/></svg>
          flowbend.com.au
        </li>
        <li>
          <svg viewBox="0 0 16 16" aria-hidden="true"><path d="M1 3h14v10H1zm1.5 1.5v.3L8 9l5.5-4.2v-.3zm0 2.2v4.8l3-2.5zm11 0l-3 2.3 3 2.5z"/></svg>
          Sales@flowbend.com.au
        </li>
      </ul>
      <address class="address">
        17 Dorwell St<br>
        Larkfield<br>
        NRT 4417
      </address>
    </div>
  </section>
</body>
</html>
```